A5 Patient Information Booklet (Chiropractic Clinic) 4-8 pages

Here’s a polished, professional rewrite of your full brief and content, with clearer structure, corrected language, and a premium tone:

---

**Project Title:** Premium Patient Information Brochure (Chiropractic & Wellness Clinic)

---

### **Overview**

We are a health and wellness clinic seeking a premium, high-end patient information brochure to provide following a patient’s initial consultation and first treatment.

The purpose of this booklet is to:

* Reinforce trust and professionalism
* Help patients understand what to expect next
* Encourage adherence to care recommendations
* Position the clinic as calm, expert-led, and results-driven

---

### **Format**

* 4–8 page booklet (A5 or similar size)
* Print-ready and digital versions required

---

### **Target Audience**

Patients who have just completed their initial consultation and may have begun treatment. They may already be experiencing physical or mental changes, so the brochure should guide, reassure, and educate them on what comes next.

---

### **Tone & Style**

* Premium, calm, and reassuring
* Modern wellness aesthetic (not overly clinical)
* Clean layout with minimal clutter
* Soft, neutral colour palette (whites, creams, muted greens, soft blues)
* Elegant typography (e.g. Montserrat / Lato)
* High-end, trustworthy, and professional feel

---

### **Key Messages**

#### 1. Listen to Your Body

Patients may feel different after treatment. Reassure them that this is normal and part of the healing process.

#### 2. Post-Treatment Advice

* Stay well hydrated
* Rest if needed
* Avoid overexertion if the body requires recovery

#### 3. Healing is a Journey (Core Concept)

A strong visual metaphor of a **“road to recovery”** or **journey** should be central to the design.

This journey should clearly illustrate three phases:

* **Phase 1: Initial Care (Weeks 1–6)**
Focus: Reducing pain/discomfort, calming the body, and initiating response to treatment

* **Phase 2: Corrective Care (Weeks 6–12)**
Focus: Addressing underlying issues, improving function, and creating lasting change

* **Phase 3: Wellness / Maintenance (Ongoing)**
Focus: Maintaining progress, preventing relapse, and supporting long-term wellbeing

**Important:**

* Emphasise that this is not a quick fix
* Progress requires time and consistency
* Each patient follows an individualised care plan
* The journey should feel structured, positive, and achievable

#### 4. Personalised Care

Reinforce that every treatment plan is tailored specifically to the individual.

#### 5. Professional Reassurance

Patients should feel confident they are in expert hands and supported throughout their journey.

---

### **Design Direction**

* Use imagery that reflects calmness, progression, and wellness (e.g. pathways, nature, soft gradients)
* Avoid generic stock imagery
* **Only use original clinic images from website and social media**
* Prioritise white space and clarity
* Aim for a luxury spa/medical hybrid aesthetic

---

## **Content Structure (Page-by-Page)**

### **Front Cover**

* Clean, minimal, premium design
* Clinic branding

---

### **Page 1: Patient Case Summary**

**Title:** *Welcome to Fernwell Spine Studio*

Thank you for choosing Fernwell Spine Studio.

This booklet is designed to guide you through:

* What we found during your initial consultation
* Your personalised recommended treatment plan
* Your road to recovery
* Long-term wellness care
* Why we take the approach we do

---

### **Page 2: Your Care Journey**

**Stage 1: Your Initial Consultation**

Today we completed a comprehensive assessment of your health and function, including:

* Full case history and discussion of your symptoms and goals
* Orthopaedic and neurological testing
* Postural and movement assessment
* Initial treatment (where appropriate)

**What this tells us:**

* How your body is currently functioning
* Where areas of stress or dysfunction may be present
* The most appropriate and effective path forward for your care

---

### **Page 3: Your Suggested Treatment Plan**

Based on today’s findings, your recommended care plan is:

**______ treatments over ______ weeks**

This should be viewed alongside your *Road to Recovery* to help you understand what to expect.

We have also discussed:

* Expected timelines for improvement
* Available payment options

**After Treatment:**
It is common to feel different following treatment. This is a normal response as your body begins to adapt and respond.

We recommend:

* Staying well hydrated
* Allowing time for rest and recovery
* Avoiding overexertion if your body feels it needs it

---

### **Page 4: What to Expect Next**

Healing is not always linear—it is a process that occurs over time.

Your care will typically progress through the following stages:

* **Relief Care**
Focused on reducing discomfort and calming the body

* **Corrective Care**
Focused on addressing underlying issues and improving function
(This phase may include prescribed exercises)

* **Maintenance / Wellness Care**
Focused on sustaining progress, preventing recurrence, and supporting long-term health

---

### **Page 5: Understanding Chiropractic Care**

**What is Chiropractic?**
Chiropractic care focuses on the relationship between the spine, nervous system, and overall body function.

By improving spinal movement and alignment, chiropractic care helps support the nervous system, allowing the body to function and heal more effectively.

**About Fernwell Spine Studio**
At Fernwell Spine Studio, our approach is centred around personalised, patient-focused care. We aim to not only relieve symptoms but to address underlying causes and support long-term wellbeing.

---

### **Back Page**

* Clinic contact details
* Website
* Social media icons/handles

**Closing Message:**
“A healthier, stronger you—supported every step of the way.”

---

### **Deliverables**

* Print-ready PDF
* Editable source files

---

### **Additional Notes**

* The brochure should feel valuable and worth keeping
* Encourage long-term care in a subtle, non-pushy way
* Maintain clarity, readability, and strong visual hierarchy
* Balance professionalism with warmth and approachability

---

If you’d like, I can also turn this into **actual brochure copy (fully written, patient-facing text)** or help you refine it further for a designer.

Existing patients who want to feel better and look after themselves that is given after their initil consultation appointment

Chiropractic, wellness, health

• Montserrat or Lato

0094D4
00A9DD
6FCCEA
C7EBF8
E9F6FB
00AB8E
00BBA5
67D7C9
C6EFE9
E9F9F6
6B429C
8869AF
B7A5CE
E3DAEB
F3F0F8

• my own photos, look premium wellness, be clear and simple to understand for patients journey or what to expect next and over time
• USe my social media/website for ideas
• generic photos and images

```html
<!DOCTYPE html>
<html lang="en">
<head>
<meta charset="utf-8">
<title>Fernwell Spine Studio – Patient Booklet</title>
<link href="https://fonts.googleapis.com/css2?family=Libre+Baskerville:ital,wght@0,400;0,700;1,400&family=Work+Sans:wght@400;500;600&display=swap" rel="stylesheet">
<style>
:root{
  --bg:#cdcdcd;
  --teal:#1ba69b;
  --teal-dark:#128c83;
  --teal-soft:#67d7c9;
  --navy:#1f2a44;
  --ink:#3a3f4a;
  --lilac:#d9c3ee;
  --lilac-soft:#f3f0f8;
  --purple:#8869af;
  --paper:#f7f7f8;
  --orange:#ef7b3a;
  --amber:#e9a521;
  --green:#8bbb3c;
}
*{box-sizing:border-box;margin:0;padding:0}
html,body{width:1200px;height:2580px;overflow:hidden}
body{background:var(--bg);font-family:"Work Sans",sans-serif;color:var(--ink);position:relative}
.spread{position:absolute;left:60px;width:1080px;height:766px;display:flex;box-shadow:0 10px 30px rgba(0,0,0,.18)}
.spread-1{top:47px}.spread-2{top:907px}.spread-3{top:1767px}
.page{position:relative;width:540px;height:766px;overflow:hidden;background:var(--paper)}
.page+.page{border-left:1px solid rgba(0,0,0,.06)}
.abs{position:absolute}
.serif{font-family:"Libre Baskerville",serif}
h2{font-family:"Libre Baskerville",serif;font-weight:700;color:var(--navy);font-size:22px;line-height:1.15}
h2 em{display:block;font-weight:400;color:var(--teal);font-style:italic}
h3{font-size:12px;font-weight:600;color:var(--navy)}
p,li{font-size:11px;line-height:1.5}
ul{list-style:none}
.photo{position:absolute;background:linear-gradient(135deg,#c9b6a8,#8d99a8 55%,#e9e4df)}

/* back cover */
.back{background:var(--teal)}
.back .photo{inset:0 0 auto 0;height:430px;background:linear-gradient(180deg,#2bb3a7,#1ba69b);opacity:.9}
.back-intro{left:60px;top:120px;width:420px;color:#fff;text-align:center;font-size:11.5px;line-height:1.6}
.plan-card{left:50px;top:330px;width:440px;height:270px;background:#f1f1f1;border-radius:26px;padding:30px 34px;text-align:center}
.plan-card h3{font-family:"Libre Baskerville",serif;font-size:17px;color:var(--navy);margin-bottom:22px}
.plan-line{font-family:"Libre Baskerville",serif;font-size:12.5px;color:var(--navy);margin:12px 0;text-align:left}
.plan-line span{display:inline-block;border-bottom:1px solid var(--navy);width:150px;height:12px}
.plan-line span.s{width:70px}
.plan-card p{color:var(--teal);margin-top:18px}
.contact{left:0;right:0;top:630px;text-align:center;color:#fff}
.contact h3{font-family:"Libre Baskerville",serif;font-size:19px;color:#fff;font-weight:400;margin-bottom:10px}
.contact p{font-family:"Libre Baskerville",serif;font-size:11px}

/* front cover */
.front{background:linear-gradient(200deg,var(--lilac) 0%,#eee6f6 40%,#f6f4fa 65%,#e7f4f5 100%)}
.cover-title{left:0;right:0;top:120px;text-align:center;font-size:30px;color:var(--navy)}
.cover-title em{color:var(--teal);font-style:normal}
.brand{left:0;right:0;top:270px;text-align:center}
.brand .ring{width:110px;height:110px;border-radius:50%;border:4px solid var(--teal-soft);margin:0 auto 22px}
.brand .name{font-family:"Libre Baskerville",serif;font-size:28px;color:var(--navy);font-weight:700;letter-spacing:.5px}
.brand .sub{font-family:"Libre Baskerville",serif;font-size:11px;color:var(--navy);letter-spacing:3px;margin-top:8px}
.cover-tagline{left:60px;right:60px;top:520px;text-align:center;font-family:"Libre Baskerville",serif;font-weight:700;font-size:17px;color:var(--navy);line-height:1.4}
.cover-strap{left:0;right:0;top:600px;text-align:center;color:var(--teal);font-size:18px}
.cover-rule{left:70px;right:70px;top:635px;height:8px}

/* icons */
.ico{width:30px;height:30px;border-radius:50%;border:1.5px solid var(--purple);flex:none;display:grid;place-items:center}
.ico i{width:10px;height:10px;border:1.5px solid var(--teal);border-radius:50%}
.find{left:40px;top:200px;display:flex;gap:10px}
.find div{width:82px;height:70px;border-radius:10px;background:#fff;box-shadow:0 2px 6px rgba(0,0,0,.08);font-size:8.5px;text-align:center;padding:28px 6px 0;position:relative;line-height:1.3}
.find div::before{content:"";position:absolute;left:31px;top:-12px;width:20px;height:20px;border-radius:6px;background:#fff;border:1.5px solid var(--purple)}
.icon-list li{display:flex;gap:10px;align-items:center;margin-bottom:12px}

/* waves */
.wave{position:absolute;left:0;width:540px}
.on-teal{color:#fff}
.on-teal h2{color:#fff}
.on-teal h2 em{color:#fff;font-style:normal;font-weight:700}
.ticks li{padding-left:16px;position:relative;margin-bottom:3px}
.ticks li::before{content:"✓";position:absolute;left:0;top:0;font-size:9px;width:11px;height:11px;border-radius:50%;background:rgba(255,255,255,.3);text-align:center;line-height:11px}

.phase h4{font-size:12px;font-weight:600}
.phase p{font-size:10.5px;line-height:1.4}
</style>
</head>
<body>

<!-- Spread 1: back and front cover -->
<section class="spread spread-1">
  <div class="page back">
    <div class="photo" role="img" aria-label="Portrait of the clinic chiropractor, tinted teal"></div>
    <p class="abs back-intro">Your Chiropractor at Fernwell Spine Studio, your care is led by chiropractor Marina, who takes a personalised, hands-on approach to your health. Every consultation is focused on understanding your body, your lifestyle, and your goals—so your treatment plan is tailored specifically to you. Marina combines clinical expertise with a calm, supportive environment to help you feel confident, informed, and in control of your recovery journey.</p>
    <div class="abs plan-card">
      <h3>Your Personalised Plan</h3>
      <div class="plan-line">Patient Name: <span style="width:260px"></span></div>
      <div class="plan-line">Your Suggested Care Plan: <span class="s"></span> treatments over <span class="s"></span> weeks</div>
      <p>Your care has been designed specifically for your needs, goals, and current condition. We're here to support you throughout your journey—with professional guidance, experience, and ongoing care.</p>
    </div>
    <div class="abs contact">
      <h3>Contact us:</h3>
      <p>12 Orchard Lane, Ashbridge, United Kingdom</p>
      <p>info@fernwellspinestudio.co.uk</p>
      <p>www.fernwellspinestudio.co.uk</p>
    </div>
  </div>
  <div class="page front">
    <h1 class="abs cover-title serif">Your Journey to<br>Better Health <em>Starts Here</em></h1>
    <div class="abs brand">
      <div class="ring"></div>
      <div class="name">Fernwell Spine Studio</div>
      <div class="sub">CHIROPRACTIC &amp; WELLNESS</div>
    </div>
    <p class="abs cover-tagline">A personalised approach to recovery, balance, and long-term wellbeing.</p>
    <p class="abs cover-strap">Guided care. Lasting results.</p>
    <svg class="abs cover-rule" viewBox="0 0 400 8" preserveAspectRatio="none"><line x1="0" y1="4" x2="400" y2="4" stroke="#1ba69b" stroke-width="1"/><circle cx="60" cy="4" r="3" fill="#1ba69b"/><circle cx="340" cy="4" r="3" fill="#1ba69b"/></svg>
  </div>
</section>

<!-- Spread 2: welcome and treatment plan -->
<section class="spread spread-2">
  <div class="page">
    <h2 class="abs" style="left:40px;top:40px">Welcome to<em>Fernwell Spine Studio</em></h2>
    <p class="abs" style="left:40px;top:105px;width:460px">Thank you for choosing Fernwell Spine Studio. We're delighted to support you on your journey toward improved health and wellbeing. This booklet has been designed to guide you through what comes next and to help you feel confident in your care.<br>Inside, you'll find:</p>
    <div class="abs find">
      <div>A summary of your initial consultation</div>
      <div>Your tailored treatment plan</div>
      <div>What to expect during your recovery</div>
      <div>Guidance for after your treatment</div>
      <div>Our long-term approach to wellness</div>
    </div>
    <p class="abs" style="left:40px;top:295px">Our goal is simple — to help you feel better, move better, and live better.</p>
    <div class="photo" style="left:0;top:340px;width:230px;height:426px" role="img" aria-label="Chiropractor assessing a seated patient's posture"></div>
    <h2 class="abs" style="left:260px;top:350px">Your<em>Care Journey</em></h2>
    <h3 class="abs" style="left:260px;top:410px">Your First Visit: What We Assessed</h3>
    <p class="abs" style="left:260px;top:430px;width:250px">During your initial consultation, we carried out a detailed assessment of your health and body function, including:</p>
    <ul class="abs icon-list" style="left:260px;top:490px;width:250px">
      <li><span class="ico"><i></i></span><p>A full discussion of your symptoms, concerns, and goals</p></li>
      <li><span class="ico"><i></i></span><p>Orthopaedic and neurological testing</p></li>
      <li><span class="ico"><i></i></span><p>Postural and movement analysis</p></li>
      <li><span class="ico"><i></i></span><p>Initial treatment (where appropriate)</p></li>
    </ul>
  </div>
  <div class="page">
    <h3 class="abs" style="left:40px;top:45px">What This Means for You</h3>
    <p class="abs" style="left:40px;top:65px;width:300px">This process helps us understand:</p>
    <ul class="abs" style="left:40px;top:84px;width:320px">
      <li>• How your body is currently functioning</li>
      <li>• Where stress, imbalance, or dysfunction may exist</li>
      <li>• The most effective and personalised path forward</li>
    </ul>
    <p class="abs" style="left:40px;top:140px;width:300px">Every recommendation we make is based on your unique needs.</p>
    <div class="abs" style="left:370px;top:80px;width:200px;height:200px;border-radius:50%;background:#fff;border:8px solid var(--lilac);display:grid;place-items:center;text-align:center">
      <span class="serif" style="font-size:13px;font-weight:700;color:var(--navy);padding:0 30px">Fernwell Spine Studio</span>
    </div>
    <h2 class="abs" style="left:40px;top:195px">Your<em>Treatment Plan</em></h2>
    <p class="abs" style="left:40px;top:255px;width:310px">Based on your assessment, your recommended care plan is:<br>______ treatments over ______ weeks<br>This plan is carefully designed to support your recovery and guide your progress step by step.<br>We have also discussed:</p>
    <ul class="abs icon-list" style="left:40px;top:345px;width:460px;display:flex;gap:30px">
      <li><span class="ico"><i></i></span><p>Expected timelines for improvement</p></li>
      <li><span class="ico"><i></i></span><p>Flexible payment options</p></li>
    </ul>
    <svg class="wave" style="top:410px;height:356px" viewBox="0 0 540 356" preserveAspectRatio="none"><path d="M0 40 C150 -10 330 80 540 30 L540 356 L0 356Z" fill="#1ba69b"/></svg>
    <div class="abs on-teal" style="left:40px;top:455px;width:320px">
      <h2>After<em>Your Treatment</em></h2>
      <p style="margin-top:10px">It is completely normal to feel different after treatment. Your body is beginning to respond and adapt — this is part of the healing process.</p>
      <h3 style="color:#fff;margin-top:8px">We Recommend:</h3>
      <ul class="ticks">
        <li>Staying well hydrated</li>
        <li>Allowing time for rest and recovery</li>
        <li>Avoiding overexertion if your body feels fatigued</li>
      </ul>
      <p>Listening to your body is key during this stage.</p>
    </div>
    <div class="photo" style="left:330px;top:590px;width:260px;height:200px;border-radius:50%" role="img" aria-label="Chiropractor treating a patient's back"></div>
  </div>
</section>

<!-- Spread 3: road to recovery and chiropractic care -->
<section class="spread spread-3">
  <div class="page">
    <h2 class="abs" style="left:40px;top:40px">Your Road<em>To Recovery</em></h2>
    <h3 class="abs" style="left:40px;top:100px">Healing is a Journey</h3>
    <p class="abs" style="left:40px;top:118px;width:460px">Recovery doesn't happen overnight. It is a gradual and structured process, unique to every individual.<br>Your care typically progresses through three key stages:</p>
    <svg class="abs" style="left:20px;top:180px" width="500" height="120" viewBox="0 0 500 120">
      <path d="M10 40 C60 20 90 30 110 40 S170 90 230 80 S320 60 380 90 S470 110 490 100" fill="none" stroke="#ef7b3a" stroke-width="5"/>
      <path d="M230 80 S320 60 380 90" fill="none" stroke="#e9a521" stroke-width="5"/>
      <path d="M380 90 S470 110 490 100" fill="none" stroke="#8bbb3c" stroke-width="5"/>
      <circle cx="95" cy="35" r="22" fill="#fff" stroke="#ef7b3a" stroke-width="2"/>
      <circle cx="240" cy="80" r="22" fill="#fff" stroke="#e9a521" stroke-width="2"/>
      <circle cx="380" cy="88" r="22" fill="#fff" stroke="#8bbb3c" stroke-width="2"/>
    </svg>
    <div class="abs phase" style="left:50px;top:245px;width:120px">
      <h4 style="color:var(--orange)">Relief Care</h4>
      <p><b>Weeks 1–6</b><br>Focus: Reducing discomfort, calming the body, and initiating healing</p>
    </div>
    <div class="abs phase" style="left:190px;top:290px;width:140px">
      <h4 style="color:var(--amber)">Corrective Care</h4>
      <p><b>Weeks 6–12</b><br>Focus: Addressing underlying issues, improving movement, and restoring function (This phase may include exercises and corrective strategies)</p>
    </div>
    <div class="abs phase" style="left:350px;top:300px;width:140px">
      <h4 style="color:var(--green)">Wellness &amp; Maintenance</h4>
      <p><b>Ongoing</b><br>Focus: Maintaining progress, preventing relapse, &amp; supporting long-term health</p>
    </div>
    <div class="photo" style="left:0;top:500px;width:250px;height:200px;border-radius:0 100px 100px 0" role="img" aria-label="Patient lying on a treatment table during an adjustment"></div>
    <h2 class="abs" style="left:270px;top:520px">What To<em>Expect Next</em></h2>
    <h3 class="abs" style="left:270px;top:580px">Understanding Your Progress</h3>
    <p class="abs" style="left:270px;top:600px;width:240px">Healing is not always linear. Some days you may feel significant improvement, while others may feel slower — this is completely normal. What matters most is steady progress over time.</p>
  </div>
  <div class="page">
    <div class="photo" style="left:30px;top:40px;width:190px;height:190px;border-radius:50%;border:6px solid var(--lilac)" role="img" aria-label="Chiropractor checking a patient's spine"></div>
    <h2 class="abs" style="left:250px;top:60px;font-size:20px">Your Care <em style="display:inline">Phases Explained</em></h2>
    <ul class="abs icon-list" style="left:250px;top:110px;width:270px">
      <li><span class="ico"><i></i></span><p><b>Relief Care</b><br>Focused on easing discomfort and reducing tension</p></li>
      <li><span class="ico"><i></i></span><p><b>Corrective Care</b><br>Focused on long-term improvements and fixing root causes</p></li>
      <li><span class="ico"><i></i></span><p><b>Wellness Care</b><br>Focused on maintaining results and supporting ongoing health</p></li>
    </ul>
    <svg class="wave" style="top:270px;height:496px" viewBox="0 0 540 496" preserveAspectRatio="none"><path d="M0 60 C160 0 340 70 540 10 L540 496 L0 496Z" fill="#1ba69b"/><path d="M0 60 C160 0 340 70 540 10" fill="none" stroke="#b7a5ce" stroke-width="6"/></svg>
    <div class="abs on-teal" style="left:40px;top:330px;width:460px">
      <h2>What is<em>Chiropractic Care?</em></h2>
      <p style="margin-top:10px">Chiropractic care focuses on the connection between your spine, nervous system, and overall body function. When spinal movement and alignment improve, your nervous system can function more effectively — helping your body heal and perform at its best.</p>
      <h2 style="margin-top:20px">Our Approach at<em>Fernwell Spine Studio</em></h2>
      <p style="margin-top:8px">At Fernwell Spine Studio, we believe in:</p>
      <ul class="ticks" style="width:250px">
        <li>Personalised, patient-focused care</li>
        <li>Treating the root cause — not just symptoms</li>
        <li>Supporting long-term health and wellbeing</li>
      </ul>
      <p style="width:250px">You're not just receiving treatment — you're investing in your future health.</p>
    </div>
    <div class="photo" style="left:310px;top:560px;width:230px;height:206px;border-radius:110px 0 0 0" role="img" aria-label="Chiropractor supporting a patient during a standing adjustment"></div>
  </div>
</section>

</body>
</html>
```